Business Report Cover

We need a revamped quarterly report cover to send to our clients. We asset manage commercial and residential properties throughout the the United States. We use a .pdf version of a cover that we've used for years but would like a fresh updated look for 2018. The cover should include our company logo (KOV Enterprises) and a photo of the property as well as the Quarter/Year of the report.

```html
<!DOCTYPE html>
<html lang="en">
<head>
<meta charset="utf-8">
<title>Quarterly Operating Report Cover</title>
<link href="https://fonts.googleapis.com/css2?family=Didact+Gothic&display=swap" rel="stylesheet">
<style>
  :root {
    --brand-green: #0e7438;
    --soft-green: #8fbfa0;
    --paper: #ffffff;
    --ink: #111111;
    --backdrop: #e9e7e3;
    --photo-sky: #d9dadc;
    --photo-ground: #5b4a48;
  }
  html, body {
    margin: 0;
    width: 1200px;
    height: 1200px;
    overflow: hidden;
    background: var(--backdrop);
    font-family: "Didact Gothic", sans-serif;
    color: var(--ink);
  }
  .report-cover {
    position: absolute;
    left: 197px;
    top: 30px;
    width: 806px;
    height: 1140px;
    background: var(--paper);
    box-shadow: 0 2px 8px rgba(0,0,0,0.18);
    overflow: hidden;
  }
  .cover-shapes {
    position: absolute;
    inset: 0;
    width: 100%;
    height: 100%;
  }
  .brand {
    position: absolute;
    left: 192px;
    top: 50px;
    line-height: 1;
  }
  .brand-name {
    display: block;
    font-size: 64px;
    letter-spacing: 1px;
  }
  .brand-sub {
    display: block;
    font-size: 12px;
    letter-spacing: 6.2px;
    margin-top: 6px;
  }
  .property-address {
    position: absolute;
    right: 35px;
    top: 42px;
    text-align: right;
    font-size: 18px;
    line-height: 25px;
    margin: 0;
    font-style: normal;
  }
  .property-photo {
    position: absolute;
    left: 192px;
    top: 174px;
    width: 614px;
    height: 570px;
    background: linear-gradient(180deg, var(--photo-sky) 0%, #c9ccd0 45%, #7c6a63 72%, var(--photo-ground) 100%);
  }
  .report-title {
    position: absolute;
    left: 189px;
    top: 776px;
    margin: 0;
    font-weight: 400;
  }
  .report-title .line {
    display: block;
    font-size: 33px;
    line-height: 42px;
    letter-spacing: -0.5px;
  }
  .report-title .year {
    display: block;
    font-size: 96px;
    line-height: 96px;
    margin-top: 0;
    letter-spacing: -2px;
  }
</style>
</head>
<body>
  <div class="report-cover">
    <svg class="cover-shapes" viewBox="0 0 984 1392" preserveAspectRatio="none" aria-hidden="true">
      <polygon points="0,0 197,0 197,910 0,1084" fill="var(--brand-green)"/>
      <polygon points="197,953 197,1023 0,1170 0,1100" fill="var(--soft-green)"/>
      <polygon points="225,1328 984,1328 984,1392 155,1392" fill="var(--brand-green)"/>
    </svg>

    <div class="brand">
      <span class="brand-name">KOV</span>
      <span class="brand-sub">ENTERPRISES</span>
    </div>

    <address class="property-address">
      Riverton Corner Mart<br>
      4120 NE Harbor Point Dr.<br>
      Riverton, WA 98600
    </address>

    <div class="property-photo" role="img" aria-label="Photo of the property: convenience store fuel canopy with pumps in front of a brick building under an overcast sky"></div>

    <h1 class="report-title">
      <span class="line">QUARTERLY OPERATING REPORT</span>
      <span class="line">1ST QUARTER</span>
      <span class="year">2018</span>
    </h1>
  </div>
</body>
</html>
```